Business Card Design

We provide services doing multiple jobs in the construction industry.Please note: The company name needs to be ROCK SOLID BUILDING SERVICESAttached logo was an example of what we wanted. Can you change up the colors?

Industry/Entity Type

Construction

Contact Information for Business Card

ROCK SOLID BUILDING SERVICES5401 HUDSON BEND RDAUSTIN, TX 78734(512)243-6854ROCKSOLIDBUILDINGSERVICES@GMAIL.COM

```html
<!DOCTYPE html>
<html lang="en">
<head>
<meta charset="utf-8">
<title>Pearlwood Framing Works – Business Card</title>
<link rel="stylesheet" href="https://fonts.googleapis.com/css2?family=Exo+2:wght@400;600;800&display=swap">
<style>
  :root {
    --navy: #1f1b66;
    --navy-deep: #15124a;
    --navy-glow: #2b2a86;
    --paper: #ffffff;
    --ink-light: #e9e9f5;
    --stage: #d9dadc;
    --brand-ink: #1f1b66;
  }
  * { box-sizing: border-box; margin: 0; padding: 0; }
  html, body { width: 1200px; height: 771px; overflow: hidden; }
  body {
    background: var(--stage);
    font-family: "Exo 2", sans-serif;
    display: flex;
    align-items: center;
    justify-content: center;
    gap: 40px;
  }
  .card {
    position: relative;
    width: 540px;
    height: 309px;
    overflow: hidden;
    box-shadow: 0 6px 18px rgba(0,0,0,0.18);
  }
  /* Front */
  .card--front { background: var(--paper); }
  .front-shape { position: absolute; inset: 0; }
  .contact-block {
    position: absolute;
    left: 30px;
    top: 30px;
    color: var(--ink-light);
  }
  .person-name {
    font-weight: 600;
    font-size: 17px;
    letter-spacing: 1.5px;
  }
  .person-role {
    font-size: 12px;
    letter-spacing: 0.5px;
    margin-top: 2px;
  }
  .address {
    font-size: 12px;
    line-height: 1.45;
    margin-top: 20px;
  }
  .contact-list {
    list-style: none;
    margin-top: 18px;
    font-size: 11.5px;
    line-height: 1.75;
  }
  .contact-list li { display: flex; align-items: center; gap: 8px; }
  .contact-icon { width: 11px; height: 11px; flex: none; }
  .front-brand {
    position: absolute;
    right: 28px;
    top: 120px;
    width: 230px;
    display: flex;
    align-items: center;
    gap: 10px;
  }
  .brand-mark {
    width: 14px;
    height: 14px;
    background: var(--brand-ink);
    flex: none;
  }
  .brand-name {
    font-weight: 800;
    font-size: 20px;
    line-height: 1.05;
    letter-spacing: 1px;
    color: var(--brand-ink);
  }
  /* Back */
  .card--back {
    background: radial-gradient(ellipse at 45% 45%, var(--navy-glow) 0%, var(--navy) 50%, var(--navy-deep) 100%);
    display: flex;
    align-items: center;
    justify-content: center;
  }
  .back-brand {
    display: flex;
    align-items: center;
    gap: 14px;
  }
  .back-brand .brand-mark { width: 20px; height: 20px; background: var(--ink-light); }
  .back-brand .brand-name { color: var(--ink-light); font-size: 30px; }
</style>
</head>
<body>
  <section class="card card--front" aria-label="Business card front">
    <svg class="front-shape" viewBox="0 0 540 309" preserveAspectRatio="none" aria-hidden="true">
      <defs>
        <radialGradient id="panelFill" cx="0.35" cy="0.45" r="0.8">
          <stop offset="0" stop-color="#2b2a86"/>
          <stop offset="1" stop-color="#17144f"/>
        </radialGradient>
      </defs>
      <path d="M0 0 H300 C262 70 230 180 226 309 H0 Z" fill="url(#panelFill)"/>
      <path d="M318 0 C278 80 246 190 244 309 H236 C238 190 268 78 310 0 Z" fill="#1f1b66"/>
    </svg>

    <div class="contact-block">
      <p class="person-name">MARCUS DELANEY</p>
      <p class="person-role">Managing Director</p>
      <p class="address">7732 Fernglen Pass Ln<br>Austin, TX 78734</p>
      <ul class="contact-list">
        <li>
          <svg class="contact-icon" viewBox="0 0 12 12" aria-hidden="true"><path d="M3 1 L5 3.5 L4 5 C4.8 6.6 5.6 7.4 7 8 L8.5 7 L11 9 L9.5 11 C5 10.5 1.5 7 1 2.5 Z" fill="currentColor"/></svg>
          (512)555-0193
        </li>
        <li>
          <svg class="contact-icon" viewBox="0 0 12 12" aria-hidden="true"><rect x="3" y="0.5" width="6" height="11" rx="1" fill="none" stroke="currentColor"/><circle cx="6" cy="9.5" r="0.7" fill="currentColor"/></svg>
          (512)555-0194
        </li>
        <li>
          <svg class="contact-icon" viewBox="0 0 12 12" aria-hidden="true"><rect x="0.5" y="2.5" width="11" height="7" fill="none" stroke="currentColor"/><path d="M0.5 2.5 L6 7 L11.5 2.5" fill="none" stroke="currentColor"/></svg>
          marcus@mailnest.example
        </li>
        <li>
          <svg class="contact-icon" viewBox="0 0 12 12" aria-hidden="true"><circle cx="6" cy="6" r="5.3" fill="none" stroke="currentColor"/><ellipse cx="6" cy="6" rx="2.3" ry="5.3" fill="none" stroke="currentColor"/><path d="M0.7 6 H11.3" stroke="currentColor"/></svg>
          www.pearlwoodframing.example
        </li>
      </ul>
    </div>

    <div class="front-brand">
      <span class="brand-mark" aria-hidden="true"></span>
      <p class="brand-name">PEARLWOOD<br>FRAMING WORKS</p>
    </div>
  </section>

  <section class="card card--back" aria-label="Business card back">
    <div class="back-brand">
      <span class="brand-mark" aria-hidden="true"></span>
      <p class="brand-name">PEARLWOOD<br>FRAMING WORKS</p>
    </div>
  </section>
</body>
</html>
```